Veltrane Group Business Card Design

The CEO is looking for a new trendy look for his business card.
You can stay with current branding or come up with something new/creative. It can be 3D, including Medical Office buildings. You can use our logo in a variety of colors. Please include name, title, company name, company website, email address, cell number

Target Market(s)

Real Estate Development and Construction

Industry/Entity Type

Health care real estate

Contact Information for Business Card

Rohesh Kamdar, CEO M-604.781.2249 E-roheshkamdar@veltrane.com Address:4180 Lindqvist Ave, Tampa, FL 33482 www.veltrane.com

Font styles to use
Other font styles liked:
• Be creative

Requirements
Must have
• Creative, trendy look
Nice to have
• Please go to our website to get a feel- www. veltrane.com
Should not have
• small fonts

```html
<!DOCTYPE html>
<html lang="en">
<head>
<meta charset="UTF-8">
<title>Veltrane Group – Business Card</title>
<link rel="stylesheet" href="https://fonts.googleapis.com/css2?family=Montserrat:wght@300;400;700;800&display=swap">
<style>
  :root {
    --stage: #1c1c1e;
    --card-white: #ffffff;
    --card-white-end: #eef0f5;
    --card-black: #141416;
    --card-black-end: #0b0b0c;
    --brand-red: #b52a38;
    --brand-navy: #1f2f55;
    --text-grey: #4a4d57;
  }
  * { box-sizing: border-box; margin: 0; padding: 0; }
  html, body { width: 1200px; height: 800px; overflow: hidden; }
  body {
    background: var(--stage);
    font-family: "Montserrat", Arial, sans-serif;
    position: relative;
  }
  .card {
    position: absolute;
    top: 110px;
    width: 340px;
    height: 580px;
    border-radius: 34px;
    border: 1.5px solid var(--brand-red);
    overflow: hidden;
  }
  .card-front {
    left: 225px;
    background: linear-gradient(150deg, var(--card-white) 45%, var(--card-white-end));
    padding: 70px 34px 44px 38px;
    display: flex;
    flex-direction: column;
  }
  .card-back {
    left: 635px;
    background: linear-gradient(160deg, var(--card-black), var(--card-black-end));
    display: flex;
    align-items: center;
    justify-content: center;
  }
  .wordmark {
    color: var(--brand-red);
    font-weight: 800;
    font-size: 38px;
    line-height: 1;
    letter-spacing: -0.5px;
    text-align: center;
  }
  .wordmark-back { font-size: 46px; }
  .holder { margin-top: auto; }
  .holder-name {
    color: var(--brand-red);
    font-weight: 700;
    font-size: 25px;
    letter-spacing: 0.5px;
    text-transform: uppercase;
    line-height: 1.1;
  }
  .holder-title {
    color: var(--brand-navy);
    font-weight: 700;
    font-size: 17px;
    margin-top: 2px;
  }
  .address {
    margin-top: 22px;
    color: var(--text-grey);
    font-weight: 400;
    font-size: 14.5px;
    line-height: 1.35;
    font-style: normal;
  }
  .contact-list {
    list-style: none;
    margin-top: 16px;
    color: var(--text-grey);
    font-size: 14px;
    line-height: 1.6;
  }
  .contact-list li { display: flex; align-items: center; gap: 10px; }
  .contact-icon { width: 14px; height: 14px; flex: none; }
</style>
</head>
<body>
  <section class="card card-front" aria-label="Business card front">
    <div class="wordmark">Veltrane Group</div>
    <div class="holder">
      <p class="holder-name">Rohesh Kamdar</p>
      <p class="holder-title">CEO</p>
      <address class="address">4180 Lindqvist Ave,<br>Tampa, FL 33482</address>
      <ul class="contact-list">
        <li>
          <svg class="contact-icon" viewBox="0 0 14 14" aria-hidden="true"><rect x="3.5" y="1" width="7" height="12" rx="1.5" fill="none" stroke="var(--brand-red)" stroke-width="1.6"/><circle cx="7" cy="10.8" r="0.9" fill="var(--brand-red)"/></svg>
          <span>604.781.2249</span>
        </li>
        <li>
          <svg class="contact-icon" viewBox="0 0 14 14" aria-hidden="true"><rect x="1" y="3" width="12" height="8.5" rx="1" fill="var(--brand-red)"/><path d="M1.5 3.5 L7 8 L12.5 3.5" fill="none" stroke="#fff" stroke-width="1.2"/></svg>
          <span>roheshkamdar@veltrane.com</span>
        </li>
        <li>
          <svg class="contact-icon" viewBox="0 0 14 14" aria-hidden="true"><circle cx="7" cy="7" r="6" fill="var(--brand-red)"/><path d="M1.5 7 H12.5 M7 1.2 C4.5 4 4.5 10 7 12.8 M7 1.2 C9.5 4 9.5 10 7 12.8" fill="none" stroke="#fff" stroke-width="0.9"/></svg>
          <span>www.veltrane.com</span>
        </li>
      </ul>
    </div>
  </section>

  <section class="card card-back" aria-label="Business card back">
    <div class="wordmark wordmark-back">Veltrane</div>
  </section>
</body>
</html>
```